VTMB site redesign

Please redesign a home page with content provided. PSD only - no coding
Can use any images from Snapwelder.com

Please create a site design that more clearly illustrates the client's services and expertise. We are looking for a high-end design.

Any images used must be generic or of Dallas TX.

Fonts: Any
Colors: Match to logo
Look: Modern - Professional

Target Market(s)

medium-large business owners

Number of Pages Required

1 page

Font styles to use
Serif
Sans Serif

Requirements
Must have
• cohesive professional design
• high end look
• Match to logo

```html
<!DOCTYPE html>
<html lang="en">
<head>
<meta charset="utf-8">
<title>VTMB — Office &amp; Warehouse Tenant Representation</title>
<link rel="stylesheet" href="https://fonts.googleapis.com/css2?family=Libre+Baskerville:wght@400;700&family=Open+Sans:wght@400;600;700&display=swap">
<style>
:root{
  --red:#c10a0a;
  --red-dark:#a50000;
  --ink:#1b1b1b;
  --text:#555;
  --muted:#8a8a8a;
  --light:#f0f0f0;
  --card:#eeeeee;
  --dark:#161616;
  --white:#fff;
  --serif:"Libre Baskerville", Georgia, serif;
  --sans:"Open Sans", Arial, sans-serif;
}
*{box-sizing:border-box;margin:0;padding:0}
html,body{width:1200px;height:4196px;overflow:hidden;background:var(--white)}
body{position:relative;font-family:var(--sans);color:var(--text)}
.abs{position:absolute}
.heading{font-family:var(--serif);font-weight:400;text-transform:uppercase;color:var(--ink);text-align:center;font-size:40px;letter-spacing:1px}
.heading em{font-style:normal;color:var(--red)}
.btn-outline{display:inline-block;border:2px solid var(--white);border-radius:6px;color:var(--white);font-family:var(--serif);text-transform:uppercase;font-size:20px;letter-spacing:1px;text-align:center;white-space:nowrap}
.photo{position:absolute}

/* header */
.site-header{position:absolute;left:0;top:0;width:1200px;height:123px;background:var(--white)}
.logo{left:78px;top:14px;width:168px;height:98px;background:var(--red);color:var(--white);font-family:var(--serif);font-weight:700;font-size:40px;display:flex;align-items:center;justify-content:center;letter-spacing:2px}
.call{right:78px;top:8px;height:30px;background:var(--red);color:var(--white);font-size:16px;display:flex;align-items:center;padding:0 14px;gap:10px}
.call strong{font-size:20px}
.nav{left:520px;top:70px;display:flex;gap:32px;align-items:center;font-size:15px;text-transform:uppercase;color:var(--ink);font-weight:600}

/* hero */
.hero{left:0;top:123px;width:1200px;height:543px;background:linear-gradient(160deg,#8fb4d9 0%,#3e6e9d 45%,#1e3d5a 75%,#5b8ab5 100%)}
.hero-arrow{top:362px;width:52px;height:52px;background:rgba(0,0,0,.45);display:flex;align-items:center;justify-content:center}
.hero-box{left:78px;top:410px;width:364px;height:380px;background:var(--red);padding:36px 26px;color:var(--white)}
.hero-box h1{font-family:var(--serif);font-weight:400;text-transform:uppercase;font-size:23px;line-height:1.5;letter-spacing:.5px;white-space:nowrap}
.hero-box p{font-style:italic;font-size:17px;line-height:1.5;margin-top:14px}
.hero-box .btn-outline{margin-top:26px;padding:14px 16px;font-size:18px}

/* why */
.card{top:915px;width:249px;height:408px;background:var(--card)}
.card .photo{left:0;top:0;width:249px;height:181px}
.card h3{position:absolute;left:12px;top:198px;font-family:var(--serif);font-weight:700;font-size:16px;color:var(--ink);text-transform:uppercase;white-space:nowrap}
.card p{position:absolute;left:12px;top:230px;width:225px;font-size:14px;line-height:1.65;color:var(--text)}

/* band */
.band{left:0;top:1547px;width:1200px;height:291px;background:var(--red)}
.band-text{left:534px;top:1600px;width:560px;color:var(--white);font-size:18px;line-height:1.6}
.band .btn-outline{position:absolute}

/* team */
.team-intro{left:145px;top:1962px;width:910px;text-align:center;font-size:14.5px;line-height:1.65;color:var(--text)}
.member{top:2064px;width:360px;text-align:center}
.member .portrait{margin:0 auto;width:156px;height:154px}
.member h4{font-family:var(--serif);font-weight:400;text-transform:uppercase;font-size:19px;color:var(--ink);margin-top:26px;white-space:nowrap}
.member span{display:block;font-size:14px;color:var(--muted);margin-top:8px}

/* testimonial */
.testimonial{left:0;top:2349px;width:1200px;height:504px;background:linear-gradient(180deg,#2a2a2a,#121212)}
.quote{left:170px;top:2630px;width:860px;text-align:center;color:#e0e0e0;font-size:15px;line-height:1.75}
.quote-name{left:0;top:2764px;width:1200px;text-align:center;color:var(--red);font-family:var(--serif);font-size:20px}

/* cta */
.cta{left:0;top:2853px;width:1200px;height:140px;background:var(--light)}
.cta p{position:absolute;left:78px;top:34px;width:700px;font-size:21px;line-height:1.6;color:#333}
.cta-btn{left:800px;top:2898px;width:322px;height:52px;background:var(--red);color:var(--white);font-family:var(--serif);text-transform:uppercase;font-size:20px;display:flex;align-items:center;justify-content:center;border-radius:4px;letter-spacing:1px;white-space:nowrap}

/* articles */
.article{top:3121px;width:333px}
.article .photo{position:relative;width:333px;height:205px}
.article h4{font-family:var(--serif);font-weight:400;font-size:19px;line-height:1.55;color:var(--ink);margin-top:20px}

/* locator */
.locator{left:0;top:3468px;width:1200px;height:582px;background:var(--red);color:var(--white);text-align:center}
.locator .heading{color:var(--white);position:absolute;left:0;top:58px;width:1200px}
.locator .heading em{color:var(--white);font-weight:700}
.locator .lead{position:absolute;left:0;top:122px;width:1200px;font-size:15px;line-height:1.85}
.field{background:#f1f1f1;height:48px;color:#999;font-size:14px;text-align:left;padding:14px 14px}
.submit{left:520px;top:3824px;width:157px;height:50px;border:2px solid var(--white);border-radius:6px;color:var(--white);font-family:var(--serif);font-size:20px;display:flex;align-items:center;justify-content:center;letter-spacing:1px}
.notices{left:0;top:3906px;width:1200px;text-align:center;color:var(--white);font-size:14.5px;line-height:2.2}
.notices .main{font-weight:700;text-decoration:underline}

/* footer */
.site-footer{left:0;top:4050px;width:1200px;height:146px;background:var(--dark);color:#bbb;font-size:14px}
.foot-item{display:flex;gap:14px;align-items:flex-start;line-height:1.85}
.social{left:607px;top:4097px;display:flex;gap:13px}
.social span{width:40px;height:40px;border-radius:50%;background:var(--red);display:block}
.copy{color:#bbb;font-size:14px}
.copy b{color:var(--red);font-weight:400}
</style>
</head>
<body>

<header class="site-header">
  <div class="abs logo">VTMB</div>
  <div class="abs call">Call Today:
    <svg width="20" height="20" viewBox="0 0 24 24"><circle cx="12" cy="12" r="11" fill="none" stroke="#fff" stroke-width="2"/><path d="M8 6l2 0 1 3-1.5 1a7 7 0 0 0 4 4l1-1.5 3 1v2c0 1-1 1.5-2 1.5A10 10 0 0 1 6.5 8c0-1 .5-2 1.5-2z" fill="#fff"/></svg>
    <strong>555-014-2626</strong></div>
  <nav class="abs nav">
    <svg width="20" height="18" viewBox="0 0 20 18"><path d="M10 1L1 9h3v8h4v-5h4v5h4V9h3z" fill="#c10a0a"/></svg>
    <span>Services</span><span>About VTMB</span><span>Contact Us</span><span>Blog</span><span>Market News</span>
    <svg width="20" height="20" viewBox="0 0 20 20"><circle cx="8" cy="8" r="6" fill="none" stroke="#1b1b1b" stroke-width="2.5"/><path d="M12.5 12.5L18 18" stroke="#1b1b1b" stroke-width="3"/></svg>
  </nav>
</header>

<section class="abs hero" role="img" aria-label="Upward view of glass office towers against a blue sky"></section>
<div class="abs hero-arrow" style="left:0"><svg width="16" height="24" viewBox="0 0 16 24"><path d="M12 3L4 12l8 9" fill="none" stroke="#fff" stroke-width="3"/></svg></div>
<div class="abs hero-arrow" style="right:0"><svg width="16" height="24" viewBox="0 0 16 24"><path d="M4 3l8 9-8 9" fill="none" stroke="#fff" stroke-width="3"/></svg></div>
<div class="abs hero-box">
  <h1>Professional<br>Office &amp;<br>Warehouse Leasing</h1>
  <p>Fast-track your search with tenant reps that only serve you, and specialize in the DFW area.</p>
  <span class="btn-outline">Contact VTMB Today!</span>
</div>

<h2 class="abs heading" style="left:0;top:842px;width:1200px">Why Tenant <em>Representation?</em></h2>

<article class="abs card" style="left:78px">
  <div class="photo" role="img" aria-label="Business handshake in front of city towers" style="background:linear-gradient(160deg,#d7e2ee,#5d7d9e)"></div>
  <h3>Relationships</h3>
  <p>Save time by trusting VTMB year after year to find the right location for you. Once we've worked together, we know what you need, and you can keep your budget details private.</p>
</article>
<article class="abs card" style="left:344px">
  <div class="photo" role="img" aria-label="Signing a non-compete agreement with a pen" style="background:linear-gradient(160deg,#f3ede6,#a98e7a)"></div>
  <h3>Access to More</h3>
  <p>We have no agreements or personal incentives for specific properties, so we can always show you the offices that are right for you.</p>
</article>
<article class="abs card" style="left:610px">
  <div class="photo" role="img" aria-label="Hand using a tablet showing a map" style="background:linear-gradient(160deg,#e9e6df,#7f8fa0)"></div>
  <h3>Free to You</h3>
  <p>You pay us nothing. We get our commission from the property being leased.</p>
</article>
<article class="abs card" style="left:873px">
  <div class="photo" role="img" aria-label="Business people touring an empty bright office" style="background:linear-gradient(160deg,#ffffff,#b8c0c8)"></div>
  <h3>Customized Service</h3>
  <p>Aside from saving you the time of repeating what your needs are to each new location, we also provide a report of the places you've seen, so it's easier to share and make a decision.</p>
</article>

<section class="abs band">
  <span class="btn-outline" style="left:534px;top:165px;width:271px;height:53px;line-height:49px">Space Calculator</span>
</section>
<div class="photo" role="img" aria-label="Handshake over a skyline of office towers" style="left:140px;top:1379px;width:344px;height:389px;background:linear-gradient(170deg,#dfe8f2,#7896b4 55%,#2e4763)"></div>
<p class="abs band-text">If you need to find office or warehouse space in the Dallas Fort Worth area, the team at VTMB has the experience you need.</p>

<h2 class="abs heading" style="left:0;top:1895px;width:1200px">Meet the <em>Team</em></h2>
<p class="abs team-intro">At VTMB we believe that you deserve the best professional advice and personal service with your commercial real estate negotiations. By choosing VTMB as your tenant reps in the Dallas/Fort Worth area, you will receive the assistance of accomplished &amp; experienced commercial real estate brokers &amp; salespeople who are licensed by the State Realty Licensing Board to practice in Texas since 1982.</p>

<div class="abs member" style="left:66px">
  <div class="portrait" role="img" aria-label="Portrait of the founder" style="background:linear-gradient(180deg,#8a8a8a,#3a3a3a)"></div>
  <h4>Graham T. Whitford</h4><span>Founder and President</span>
</div>
<div class="abs member" style="left:418px">
  <div class="portrait" role="img" aria-label="Portrait of the senior director" style="background:linear-gradient(180deg,#8a8a8a,#3a3a3a)"></div>
  <h4>Mark Ellison-Reed</h4><span>Senior Director, Commercial Property Specialist</span>
</div>
<div class="abs member" style="left:773px">
  <div class="portrait" role="img" aria-label="Portrait of the associate" style="background:linear-gradient(180deg,#8a8a8a,#3a3a3a)"></div>
  <h4>Daniel Thomas Carver RP</h4><span>Associate, Tenant Rep Specialist</span>
</div>

<section class="abs testimonial" role="img" aria-label="Dark aerial view of a dense city skyline"></section>
<h2 class="abs heading" style="left:0;top:2406px;width:1200px;color:#fff">What Our <em>Client Say</em></h2>
<div class="abs" role="img" aria-label="Client portrait" style="left:539px;top:2480px;width:124px;height:124px;border-radius:50%;border:5px solid var(--red);background:linear-gradient(180deg,#ddd,#888)"></div>
<div class="abs" style="left:634px;top:2478px;width:40px;height:40px;border-radius:50%;background:var(--red);color:#fff;font-family:var(--serif);font-size:34px;text-align:center;line-height:48px">&ldquo;</div>
<p class="abs quote">"The real estate team at VTMB has decades of experience in Commercial. One advantage of VTMB is they know all the properties that are about to become available, BEFORE they are available. They have the inside track on properties and they watch your back at the negotiating table. Very impressive with a polished approach. Let the team run with your next project &amp; you won't be disappointed."</p>
<p class="abs quote-name">&mdash; Jonathan Paul Kessler</p>

<section class="abs cta"><p>Whether your lease is expiring soon, or you're just starting your search, VTMB can help you find the perfect space.</p></section>
<div class="abs cta-btn">Make an Appointment</div>

<h2 class="abs heading" style="left:0;top:3047px;width:1200px">Latest <em>Articles</em></h2>
<article class="abs article" style="left:78px">
  <div class="photo" role="img" aria-label="Architectural sketch of an office building" style="background:linear-gradient(160deg,#f4f4f4,#a9afb5)"></div>
  <h4>6 Important Key Aspects of Tenant Representation To Know !</h4>
</article>
<article class="abs article" style="left:434px">
  <div class="photo" role="img" aria-label="Upward view of office skyscrapers" style="background:linear-gradient(160deg,#a7c2dc,#2f4d6b)"></div>
  <h4>How Dose Landlord Recapture Relate To My Office Lease ?</h4>
</article>
<article class="abs article" style="left:789px">
  <div class="photo" role="img" aria-label="Business people in an empty office space" style="background:linear-gradient(160deg,#ffffff,#b8c0c8)"></div>
  <h4>Shared Building Amenities - Is Your Office Space Growing ?</h4>
</article>

<section class="abs locator">
  <h2 class="heading"><em>Free</em> Locator</h2>
  <p class="lead">Looking for commercial real estate in the DFW area? Fill out the form below and use our<br>FREE location service to find it for you!</p>
</section>
<div class="abs field" style="left:148px;top:3664px;width:291px">Name *</div>
<div class="abs field" style="left:456px;top:3664px;width:291px">Email *</div>
<div class="abs field" style="left:758px;top:3664px;width:291px">Phone *</div>
<div class="abs field" style="left:148px;top:3723px;width:901px;height:87px">Message *</div>
<div class="abs submit">SUBMIT</div>
<div class="abs notices">
  <div class="main">State Realty Licensing Board Mandated Disclosure Notices &ndash; click links below to view pages</div>
  <div>State Realty Licensing Board Information About Brokerage Services</div>
  <div>State Realty Licensing Board Consumer Protection Notice</div>
</div>

<footer class="abs site-footer">
  <div class="abs foot-item" style="left:103px;top:36px">
    <svg width="16" height="22" viewBox="0 0 16 22"><path d="M8 0a8 8 0 0 0-8 8c0 6 8 14 8 14s8-8 8-14a8 8 0 0 0-8-8z" fill="#c10a0a"/><circle cx="8" cy="8" r="3" fill="#161616"/></svg>
    <span>410 Cedar Ridge Ave, Suite<br>850, Dallas, TX 75201</span>
  </div>
  <div class="abs foot-item" style="left:340px;top:36px">
    <div style="display:flex;flex-direction:column;gap:10px;padding-top:4px">
      <svg width="18" height="18" viewBox="0 0 24 24"><path d="M5 2l4 0 2 5-2.5 1.5a11 11 0 0 0 7 7L17 13l5 2v4c0 2-1.5 3-3 3A17 17 0 0 1 2 5c0-1.5 1-3 3-3z" fill="#c10a0a"/></svg>
      <svg width="18" height="18" viewBox="0 0 24 24"><rect x="2" y="8" width="20" height="12" rx="2" fill="#c10a0a"/><rect x="6" y="2" width="12" height="8" fill="#c10a0a"/><rect x="7" y="13" width="10" height="2" fill="#161616"/></svg>
    </div>
    <span>555-014-2626<br>555-014-3299</span>
  </div>
  <div class="abs copy" style="left:875px;top:58px">&copy; <b>VTMB</b> - 2016 All Right Reserved.</div>
</footer>
<div class="abs social" aria-label="Social links"><span></span><span></span><span></span><span></span></div>

</body>
</html>
```